Wordpress Design for a Private Label BBQ Brand

For our new brand, we'd need a new Wordpress website. We'd prefer to run the website on Wordpress

We'd like to include the following
- space for description of the brand
- space for product portfolio (not a shop!)
- space for socials
- space for support
- space for contact

```html
<!DOCTYPE html>
<html lang="en">
<head>
<meta charset="utf-8">
<title>Brazora — BBQ</title>
<link href="https://fonts.googleapis.com/css2?family=Cinzel:wght@700&family=Libre+Baskerville:wght@400;700&family=Montserrat:wght@600;700&family=Figtree:wght@400;500&display=swap" rel="stylesheet">
<style>
:root{
  --red:#c0161f;
  --orange:#ec6a20;
  --ember:#e85a1c;
  --ink:#111;
  --text:#2b2b2b;
  --muted:#f0f0f0;
  --line:#d9d9d9;
  --white:#fff;
  --grad:linear-gradient(180deg,var(--red),var(--orange));
  --grad-h:linear-gradient(90deg,var(--red),var(--orange));
}
*{margin:0;padding:0;box-sizing:border-box}
html,body{width:1200px;height:4027px;overflow:hidden}
body{position:relative;font-family:"Figtree",sans-serif;color:var(--text);background:var(--white)}
.abs{position:absolute}

/* header */
.topbar{left:0;top:0;width:1200px;height:110px;background:var(--white);z-index:3}
.brand{left:98px;top:28px;font-family:"Libre Baskerville",serif;font-weight:700;font-size:36px;color:var(--ink);display:flex;align-items:center;gap:10px;white-space:nowrap}
.brand .dot{width:22px;height:22px;border-radius:50%;background:var(--red)}
.contact-line{top:18px;display:flex;align-items:center;gap:10px;font-size:16px;white-space:nowrap}
.contact-line .ic{width:32px;height:32px;border-radius:50%;background:var(--red);display:flex;align-items:center;justify-content:center}
.contact-line .lbl{color:var(--red)}
.btn{background:var(--grad-h);color:var(--white);font-family:"Montserrat",sans-serif;font-weight:700;display:flex;align-items:center;justify-content:center;border-radius:3px;box-shadow:4px 4px 0 rgba(0,0,0,.12);white-space:nowrap}
.btn-top{left:940px;top:12px;width:162px;height:46px;font-size:19px}
.nav{left:385px;top:70px;width:815px;height:50px;z-index:4;background:var(--grad-h);clip-path:polygon(40px 0,100% 0,100% 100%,0 100%);display:flex;align-items:center;padding-left:88px;gap:38px}
.nav a{color:var(--white);text-decoration:none;font-family:"Libre Baskerville",serif;font-size:17px;white-space:nowrap}

/* hero */
.hero{left:0;top:110px;width:1200px;height:580px;background:radial-gradient(ellipse at 50% 85%,#ff9a1e 0%,#e2420c 35%,#6a1205 62%,#0b0302 90%)}
.hero-title{top:206px;width:1200px;text-align:center;font-family:"Cinzel",serif;font-size:52px;color:var(--white);letter-spacing:1px}
.hero-sub{top:272px;width:1200px;text-align:center;font-family:"Libre Baskerville",serif;font-size:18px;color:var(--white)}
.btn-hero{left:520px;top:312px;width:160px;height:45px;font-size:18px}

/* about */
.about-img{top:785px;width:273px;height:398px;background:linear-gradient(180deg,var(--red),var(--orange));box-shadow:3px 3px 6px rgba(0,0,0,.15)}
.sec-title{width:1200px;text-align:center;font-family:"Montserrat",sans-serif;font-weight:700;font-size:31px;color:var(--ink);display:flex;justify-content:center;align-items:center;gap:12px}
.sec-title .dot{width:18px;height:18px;border-radius:50%;background:var(--red)}
.about-text{left:355px;top:834px;width:490px;text-align:center;font-size:15px;line-height:31px}
.btn-about{left:518px;top:1135px;width:162px;height:47px;font-size:19px}

/* portfolio */
.portfolio{left:0;top:1259px;width:1200px;height:871px;background:radial-gradient(ellipse at 40% 40%,#f08a3c,#e05e1b 60%,#c8420f)}
.card{background:var(--muted);border-bottom-right-radius:64px}

/* faq */
.faq{left:230px;width:740px;border:1px solid var(--line);border-radius:4px;box-shadow:0 2px 4px rgba(0,0,0,.06);padding:0 28px;font-size:16px;color:var(--ink)}
.faq .q{height:70px;display:flex;align-items:center;justify-content:space-between}
.faq .plus{font-size:30px;font-weight:400;line-height:1}
.faq.open{background:var(--grad);color:var(--white);border:none}
.faq.open p{line-height:30px;font-size:16px}

/* reviews */
.reviews{left:0;top:2831px;width:1200px;height:504px;background:var(--grad)}
.quote-ring{left:556px;top:2952px;width:88px;height:88px;border:2px solid var(--white);border-radius:50%;display:flex;align-items:center;justify-content:center;color:var(--white);font-family:"Libre Baskerville",serif;font-size:44px;padding-top:20px}
.review-text{top:3060px;width:1200px;text-align:center;color:var(--white);font-size:17px;line-height:33px}
.social{display:flex;gap:32px;justify-content:center;width:1200px}
.social span{width:26px;height:26px;border-radius:50%}

/* contact */
.contact-text{top:3456px;left:170px;width:860px;text-align:center;font-size:15px;line-height:31px;color:var(--ink)}
.contact-item{top:3528px;display:flex;align-items:center;gap:34px;font-size:17px;color:var(--ink);white-space:nowrap}
.contact-item .box{width:50px;height:50px;background:var(--grad);display:flex;align-items:center;justify-content:center;box-shadow:3px 3px 4px rgba(0,0,0,.15)}

/* footer */
.footer{left:0;top:3677px;width:1200px;height:350px;background:#000}
.footer-brand{top:3738px;width:1200px;text-align:center;font-family:"Libre Baskerville",serif;font-weight:700;font-size:46px;color:var(--white);display:flex;justify-content:center;align-items:center;gap:12px}
.footer-brand .dot{width:26px;height:26px;border-radius:50%;background:var(--white)}
.footer-nav{top:3818px;width:1200px;display:flex;justify-content:center;gap:52px}
.footer-nav a{color:var(--white);text-decoration:none;font-family:"Montserrat",sans-serif;font-weight:600;font-size:15px}
.footer-rule{left:98px;top:3958px;width:1004px;height:1px;background:#555}
.copyright{top:3980px;width:1200px;text-align:center;color:var(--white);font-family:"Montserrat",sans-serif;font-weight:600;font-size:14px}
</style>
</head>
<body>

<header>
  <div class="abs topbar"></div>
  <div class="abs brand" style="z-index:5"><span class="dot"></span>BRAZORA</div>
  <div class="abs contact-line" style="left:424px;z-index:5">
    <span class="ic"><svg width="16" height="12" viewBox="0 0 16 12"><rect x="1" y="1" width="14" height="10" rx="1" fill="none" stroke="#fff" stroke-width="1.6"/><path d="M1 2l7 5 7-5" fill="none" stroke="#fff" stroke-width="1.6"/></svg></span>
    <span><span class="lbl">Mail :</span> info@brazora.com</span>
  </div>
  <div class="abs contact-line" style="left:658px;z-index:5">
    <span class="ic"><svg width="16" height="16" viewBox="0 0 24 24"><path fill="#fff" d="M6.6 10.8a15 15 0 006.6 6.6l2.2-2.2c.3-.3.7-.4 1-.2 1.1.4 2.3.6 3.6.6.6 0 1 .4 1 1V20c0 .6-.4 1-1 1A17 17 0 013 4c0-.6.4-1 1-1h3.5c.6 0 1 .4 1 1 0 1.3.2 2.5.6 3.6.1.3 0 .7-.2 1z"/></svg></span>
    <span><span class="lbl">Call Now :</span> +1 555 010 2040</span>
  </div>
  <a class="abs btn btn-top" style="z-index:5">Contact Us</a>
  <nav class="abs nav">
    <a>Home</a><a>About Us</a><a>Product Portfolio</a><a>Socials</a><a>Support</a><a>Contact</a>
  </nav>
</header>

<section>
  <div class="abs hero" role="img" aria-label="Flames rising through a barbecue grill grate"></div>
  <h1 class="abs hero-title">WELCOME TO BRAZORA</h1>
  <p class="abs hero-sub">Lorem Ipsum is simply dummy text of the printing and typesetting industry.</p>
  <a class="abs btn btn-hero">Order Now</a>
</section>

<section>
  <div class="abs about-img" style="left:70px" role="img" aria-label="Black ceramic kamado grill, lid closed"></div>
  <div class="abs about-img" style="left:855px" role="img" aria-label="Black ceramic kamado grill, lid open"></div>
  <h2 class="abs sec-title" style="top:772px"><span class="dot"></span>ABOUT US</h2>
  <p class="abs about-text">Sed ut perspiciatis unde omnis iste natus error sit voluptatem accusantium doloremque laudantium, totam rem aperiam, eaque ipsa quae ab illo inventore veritatis et quasi architecto beatae vitae dicta sunt explicabo. Nemo enim ipsam voluptatem quia voluptas sit aspernatur aut odit aut fugit, sed quia consequuntur magni dolores eos qui ratione voluptatem sequi nesciunt. Neque porro quisquam est, qui dolorem ipsum quia dolor sit amet, consectetur, adipisci velit, sed quia non numquam eius modi tempora incidunt ut labore et dolore magnam aliquam quaerat voluptatem.</p>
  <a class="abs btn btn-about">Order Now</a>
</section>

<section>
  <div class="abs portfolio" role="img" aria-label="Orange-tinted grill grate over glowing coals"></div>
  <h2 class="abs sec-title" style="top:1336px;color:var(--white)"><span class="dot" style="background:var(--white)"></span>PRODUCT PORTFOLIO</h2>
  <div class="abs card" style="left:98px;top:1416px;width:497px;height:299px" role="img" aria-label="Kamado grill seen from the front with open lid and grate"></div>
  <div class="abs card" style="left:605px;top:1416px;width:497px;height:299px" role="img" aria-label="Base of kamado grill with vent door"></div>
  <div class="abs card" style="left:98px;top:1729px;width:325px;height:300px" role="img" aria-label="Aluminium carry case"></div>
  <div class="abs card" style="left:434px;top:1729px;width:326px;height:300px" role="img" aria-label="Stainless grill scraper"></div>
  <div class="abs card" style="left:772px;top:1729px;width:325px;height:300px" role="img" aria-label="Barbecue tool set: tongs, fork and spatula"></div>
</section>

<section>
  <h2 class="abs sec-title" style="top:2195px"><span class="dot"></span>FREQUENTLY ASKED QUESTIONS</h2>
  <div class="abs faq" style="top:2264px"><div class="q"><span>1. Sed ut perspiciatis unde omnis iste natus error sit voluptatem</span><span class="plus">+</span></div></div>
  <div class="abs faq open" style="top:2358px;height:182px">
    <div class="q" style="height:66px"><span>2. Where can I get some?</span><span class="plus">—</span></div>
    <p>Lorem ipsum dolor sit amet, consectetur adipiscing elit, sed do eiusmod tempor incididunt ut labore et dolore magna aliqua. Ut enim ad minim veniam, quis nostrud exercitation ullamco laboris nisi ut aliquip ex ea commodo consequat.</p>
  </div>
  <div class="abs faq" style="top:2566px"><div class="q"><span>3. What is Lorem Ipsum?</span><span class="plus">+</span></div></div>
  <div class="abs faq" style="top:2666px"><div class="q"><span>4. Where does it come from?</span><span class="plus">+</span></div></div>
</section>

<section>
  <div class="abs reviews"></div>
  <h2 class="abs sec-title" style="top:2886px;color:var(--white)"><span class="dot" style="background:var(--white)"></span>CLIENT REVIEWS</h2>
  <div class="abs quote-ring">”</div>
  <p class="abs review-text">“Nam libero tempore, cum soluta nobis est eligendi optio cumque nihil impedit quo minus id quod<br>maxime placeat facere possimus, omnis voluptas assumenda est, omnis dolor repellendus.<br>Temporibus autem quibusdam et aut officiis debitis aut rerum necessitatib.”</p>
  <p class="abs review-text" style="top:3170px;line-height:27px">- LOREM IPSUM<br>Nam libero tempore</p>
  <div class="abs social" style="top:3244px"><span style="background:#fff"></span><span style="background:#fff"></span><span style="background:#fff"></span><span style="background:#fff"></span></div>
</section>

<section>
  <h2 class="abs sec-title" style="top:3398px"><span class="dot"></span>CONTACT US</h2>
  <p class="abs contact-text">Lorem Ipsum is simply dummy text of the printing and typesetting industry. Lorem Ipsum has been the industry's standard dummy text.</p>
  <div class="abs contact-item" style="left:140px">
    <span class="box"><svg width="24" height="18" viewBox="0 0 16 12"><rect x="1" y="1" width="14" height="10" rx="1" fill="#fff"/><path d="M1 2l7 5 7-5" fill="none" stroke="#d9331c" stroke-width="1.4"/></svg></span>info@brazora.com
  </div>
  <div class="abs contact-item" style="left:490px">
    <span class="box"><svg width="20" height="26" viewBox="0 0 20 26"><path fill="#fff" d="M10 0a9 9 0 00-9 9c0 7 9 17 9 17s9-10 9-17a9 9 0 00-9-9z"/><circle cx="10" cy="9" r="3.5" fill="#d9331c"/></svg></span>Brazora, United States.
  </div>
  <div class="abs contact-item" style="left:849px;gap:20px">
    <span class="box"><svg width="22" height="22" viewBox="0 0 24 24"><path fill="#fff" d="M6.6 10.8a15 15 0 006.6 6.6l2.2-2.2c.3-.3.7-.4 1-.2 1.1.4 2.3.6 3.6.6.6 0 1 .4 1 1V20c0 .6-.4 1-1 1A17 17 0 013 4c0-.6.4-1 1-1h3.5c.6 0 1 .4 1 1 0 1.3.2 2.5.6 3.6.1.3 0 .7-.2 1z"/></svg></span>+1 555 010 2040
  </div>
</section>

<footer>
  <div class="abs footer"></div>
  <div class="abs footer-brand"><span class="dot"></span>BRAZORA</div>
  <nav class="abs footer-nav"><a>HOME</a><a>ABOUT US</a><a>PRODUCT PORTFOLIO</a><a>SOCIALS</a><a>SUPPORT</a><a>CONTACT</a></nav>
  <div class="abs social" style="top:3863px"><span style="background:var(--orange)"></span><span style="background:var(--orange)"></span><span style="background:var(--orange)"></span><span style="background:var(--orange)"></span></div>
  <div class="abs footer-rule"></div>
  <p class="abs copyright">COPYRIGHTS@2023.BRAZORA.ALL RIGHTS RESERVED</p>
</footer>

</body>
</html>
```